Business Card Design for Flood Rescue 360 - Property Restoration Professionals

I need a business card designed for Flood Rescue 360. We are a full-service property restoration solution. Providing water, fire, smoke & storm restoration as well as mold remediation and full remodel or reconstruction to homes and businesses across Dallas-Fort Worth, TX.
Target Market(s)
home and business owners with insurance covered property damage from water, fire or storm related damage
Industry/Entity Type
property restoration
Contact Information for Business Card
Marcus Pelley General Manager Cell: 214-555-0193 Office: 469-555-0148 email: Marcus@FloodRescue360.example services: Water, Fire, Mold, Reconstruction Tagline: Urgency for Your Water Emergency!
Look and feel
Each slider illustrates characteristics of the customer's brand and the style your logo design should communicate.

```html
<!DOCTYPE html>
<html lang="en">
<head>
<meta charset="utf-8">
<title>Flood Rescue 360 – Business Card</title>
<link href="https://fonts.googleapis.com/css2?family=Montserrat:wght@400;500;700;800;900&display=swap" rel="stylesheet">
<style>
  :root {
    --bg: #cfd4d5;
    --card: #f1f1f0;
    --brand-blue: #0bb0e6;
    --ink-grey: #3a3a3a;
    --mid-grey: #7a7a7a;
  }
  * { margin: 0; padding: 0; box-sizing: border-box; }
  html, body { width: 1200px; height: 881px; overflow: hidden; }
  body {
    background: var(--bg);
    font-family: "Montserrat", Arial, sans-serif;
    position: relative;
  }
  .card {
    position: absolute;
    width: 540px;
    height: 309px;
    background: var(--card);
    border-bottom: 6px solid var(--brand-blue);
    box-shadow: 0 18px 30px rgba(0,0,0,0.18);
  }
  .card--front { left: 50px; top: 450px; }
  .card--back { left: 610px; top: 120px; }

  /* brand name lockup */
  .brand { display: flex; align-items: center; gap: 12px; color: var(--brand-blue); font-weight: 900; text-transform: uppercase; line-height: 0.9; }
  .brand__dot { flex: none; border-radius: 50%; background: var(--brand-blue); }

  /* front */
  .front__brand { position: absolute; left: 30px; top: 62px; font-size: 36px; }
  .front__brand .brand__dot { width: 34px; height: 34px; }
  .front__divider { position: absolute; left: 268px; top: 50px; width: 2px; height: 150px; background: var(--brand-blue); }
  .front__details { position: absolute; left: 286px; top: 50px; }
  .person__name { color: var(--brand-blue); font-weight: 800; font-size: 24px; }
  .person__title { color: var(--ink-grey); font-size: 14px; margin: 2px 0 12px; }
  .contact { list-style: none; }
  .contact__item { display: flex; align-items: center; gap: 8px; font-size: 13px; color: var(--ink-grey); line-height: 1.55; }
  .contact__item svg { width: 12px; height: 12px; flex: none; fill: var(--brand-blue); }
  .front__tagline { position: absolute; left: 0; right: 0; bottom: 30px; text-align: center; font-size: 15px; color: var(--ink-grey); }

  /* back */
  .back__brand { position: absolute; left: 50px; top: 70px; font-size: 54px; width: 460px; }
  .back__brand .brand__dot { width: 80px; height: 80px; }
  .back__label { position: absolute; left: 0; right: 0; top: 200px; text-align: center; color: var(--brand-blue); font-weight: 800; font-size: 18px; letter-spacing: 1px; }
  .services { position: absolute; left: 0; right: 0; top: 236px; display: flex; justify-content: center; align-items: center; gap: 8px; font-size: 15px; color: var(--ink-grey); }
  .services__sep { width: 8px; height: 8px; border-radius: 50%; background: var(--brand-blue); }
</style>
</head>
<body>

<section class="card card--front" aria-label="Business card front">
  <div class="brand front__brand">
    <span>Flood<br>Rescue<br>360</span>
    <span class="brand__dot"></span>
  </div>
  <div class="front__divider"></div>
  <div class="front__details">
    <p class="person__name">Marcus Pelley</p>
    <p class="person__title">General Manager</p>
    <ul class="contact">
      <li class="contact__item"><svg viewBox="0 0 12 12"><rect x="3" y="0" width="6" height="12" rx="1"/></svg>214-555-0193</li>
      <li class="contact__item"><svg viewBox="0 0 12 12"><path d="M1 4 Q6 0 11 4 L9 6 L8 4.5 Q6 4 4 4.5 L3 6 Z M2 7 H10 V11 H2 Z"/></svg>469-555-0148</li>
      <li class="contact__item"><svg viewBox="0 0 12 12"><path d="M0 2 H12 V10 H0 Z" /></svg>Marcus@FloodRescue360.example</li>
      <li class="contact__item"><svg viewBox="0 0 12 12"><circle cx="6" cy="6" r="6"/></svg>FloodRescue360.example</li>
    </ul>
  </div>
  <p class="front__tagline">Urgency for Your Water Emergency!</p>
</section>

<section class="card card--back" aria-label="Business card back">
  <div class="brand back__brand">
    <span>Flood Rescue<br>360</span>
    <span class="brand__dot"></span>
  </div>
  <p class="back__label">SERVICES</p>
  <p class="services">
    <span>Water</span><span class="services__sep"></span>
    <span>Fire</span><span class="services__sep"></span>
    <span>Mold</span><span class="services__sep"></span>
    <span>Reconstruction</span>
  </p>
</section>

</body>
</html>
```